Larvik GmbH needs a sensational homepage!

A draft of the performances and the logo were uploaded in the attachment. The homepage should be adapted to the colors of the logo. Either pictures, graphics or icons of the respective topic are to be used for the buttons. Social media Linkedin, Youtube, Instagram should not be missing. An imprint, contact form with telephone number and email address should be given on the home page. The page should definitely be designed to be responsive for all end devices. Texts as well as images and videos are inserted in the sub-menus or pages. Only the structure and a simple application should be given. We have already secured the domain www.larvik-demo.at.
We are a young, dynamic company with a high technical affinity. Ask for creative suggestions. If something is needed, please contact us.

Target Market(s)

Construction industry, client

Requirements
Must have
• see description
Should not have
• shouldn't be colorful and playful

```html
<!DOCTYPE html>
<html lang="en">
<head>
<meta charset="utf-8">
<title>Larvik GmbH</title>
<link rel="stylesheet" href="https://fonts.googleapis.com/css2?family=Lora:wght@400;500&family=Arimo:wght@400&family=Mulish:wght@400;600&display=swap">
<style>
:root{
  --ink:#263a45;
  --navy:#243741;
  --navy-deep:#21323b;
  --text:#4a4a4a;
  --grey:#9a9fa3;
  --paper:#ffffff;
  --mist:#eff0f2;
  --line:#8a969c;
}
*{box-sizing:border-box;margin:0;padding:0}
html,body{width:1200px;height:2535px;overflow:hidden;background:var(--paper)}
body{position:relative;font-family:"Arimo",Arial,sans-serif;color:var(--text)}
h1,h2{font-weight:400}

/* header */
.site-header{position:absolute;left:0;top:0;width:1200px;height:133px;background:var(--paper)}
.brand{position:absolute;left:112px;top:40px;display:flex;align-items:center;gap:14px;font-family:"Lora",Georgia,serif;font-weight:400;font-size:50px;letter-spacing:11px;color:#4a4f55;line-height:1}
.brand-mark{width:15px;height:15px;background:#4a4f55}
.main-nav{position:absolute;top:58px;left:679px;display:flex;gap:43px;font-family:"Lora",Georgia,serif;font-size:14.5px;color:var(--ink)}

/* hero */
.hero{position:absolute;left:0;top:133px;width:1200px;height:693px}
.hero-photo{position:absolute;inset:0;background:linear-gradient(120deg,#6e7f8d 0%,#3b4e5e 45%,#1d3040 100%)}
.hero-title{position:absolute;left:0;width:1200px;top:228px;text-align:center;font-family:"Lora",Georgia,serif;font-weight:400;font-size:112px;letter-spacing:28px;color:#fff;line-height:1;padding-left:28px}
.hero-sub{position:absolute;left:0;width:1200px;top:360px;text-align:center;font-family:"Lora",Georgia,serif;font-size:21px;line-height:38px;color:#f2f4f6}
.btn-outline{position:absolute;left:495px;top:448px;width:210px;height:59px;border:2px solid #fff;border-radius:30px;color:#fff;font-family:"Lora",Georgia,serif;font-size:19px;display:flex;align-items:center;justify-content:center}

/* about */
.about-title{position:absolute;left:112px;top:874px;font-family:"Lora",Georgia,serif;font-size:38px;color:var(--ink)}
.rule{position:absolute;height:3px;width:48px;background:var(--ink)}
.about-copy{position:absolute;left:112px;top:975px;width:448px;font-size:13.8px;line-height:25.8px;color:var(--text)}
.about-copy p+p{margin-top:25.8px}
.btn-solid{position:absolute;background:var(--ink);color:#fff;font-family:"Lora",Georgia,serif;display:flex;align-items:center;justify-content:center;border-radius:30px}
.about-photo{position:absolute;left:610px;top:826px;width:590px;height:542px;background:linear-gradient(135deg,#dce6ef 0%,#b7cbdc 55%,#8ea8bf 100%)}

/* services */
.services{position:absolute;left:0;top:1368px;width:1200px;height:645px}
.services-bg{position:absolute;inset:0;background:linear-gradient(180deg,#f1f1f3 0%,#eceef1 60%,#e6e9ec 100%)}
.services-title{position:absolute;left:0;width:1200px;top:1434px;text-align:center;font-family:"Lora",Georgia,serif;font-size:38px;color:var(--ink)}
.service-card{position:absolute;top:1530px;width:312px;height:399px;border:4px solid #111;text-align:center}
.service-card svg{position:absolute;left:50%;top:34px;transform:translateX(-50%)}
.service-name{position:absolute;left:0;width:100%;top:147px;font-family:"Lora",Georgia,serif;font-size:17.5px;color:var(--ink)}
.service-text{position:absolute;left:22px;width:260px;top:196px;font-size:14px;line-height:25.8px;color:#555}
.service-card .btn-solid{left:84px;top:316px;width:140px;height:48px;font-size:15px}

/* contact */
.contact{position:absolute;left:0;top:2013px;width:1200px;height:437px;background:var(--navy)}
.contact-title{position:absolute;left:130px;top:2066px;font-family:"Lora",Georgia,serif;font-size:26px;color:#fff}
.info-item{position:absolute;left:130px;color:#fff}
.info-item svg{position:absolute;left:0;top:0}
.info-label{position:absolute;left:65px;top:0;font-family:"Mulish",Arial,sans-serif;font-weight:600;font-size:17px;white-space:nowrap}
.info-value{position:absolute;left:65px;top:28px;font-size:14px;white-space:nowrap}
.field{position:absolute;border-bottom:1px solid var(--line);font-family:"Mulish",Arial,sans-serif;font-size:16px;color:#e6ebee;padding-bottom:11px}
.btn-submit{position:absolute;left:556px;top:2355px;width:168px;height:52px;border-radius:26px;background:var(--grey);color:#fff;font-family:"Mulish",Arial,sans-serif;font-weight:600;font-size:18px;display:flex;align-items:center;justify-content:center;letter-spacing:.5px}
.social{position:absolute;top:2359px;width:37px;height:37px;border:2px solid #fff;border-radius:50%}

/* footer */
.site-footer{position:absolute;left:0;top:2450px;width:1200px;height:85px;background:var(--navy-deep);border-top:1px solid #2e434e}
.copyright{position:absolute;left:0;width:1200px;top:33px;text-align:center;font-size:14.5px;color:#e8ecee}
</style>
</head>
<body>

<header class="site-header">
  <div class="brand"><span class="brand-mark"></span>LARVIK</div>
  <nav class="main-nav"><span>HOME</span><span>ABOUT US</span><span>SERVICES</span><span>CONTACT US</span></nav>
</header>

<section class="hero">
  <div class="hero-photo" role="img" aria-label="Business team reviewing charts and reports on a desk, blue-toned photo"></div>
  <h1 class="hero-title">LARVIK</h1>
  <p class="hero-sub">Sed ut perspiciatis unde omnis iste natus error sit voluptatem<br>laudantium accusantium doloremque</p>
  <a class="btn-outline">LEARN MORE</a>
</section>

<h2 class="about-title">ABOUT US</h2>
<div class="rule" style="left:112px;top:937px"></div>
<div class="about-copy">
  <p>Sed ut perspiciatis unde omnis iste natus error sit voluptatem accusant ium doloremque laudantium, totam rem aperiam, eaque ipsa quae ab illo inventore veritatis et quasi architecto beatae vitae dicta sunt explica bo. Nemo enim ipsam voluptatem quia voluptas sit aspernatur aut odit aut volupt aiste natus error tem sequi nesciunt.</p>
  <p>Neque porro quisquam est, qui dolorem ipsum quia dolor sit amet, cons ectetur, adipisci velit, sed quia non numquam eius modi tempora incidu nt ut labore et dolore magnam aliquam quaerat voluptatem.</p>
</div>
<a class="btn-solid" style="left:112px;top:1237px;width:163px;height:56px;font-size:16px">READ MORE</a>
<div class="about-photo" role="img" aria-label="Smiling businessman in a light shirt seated on a sofa holding a tablet"></div>

<section class="services">
  <div class="services-bg" role="img" aria-label="Faint background photo of a businessman in an office"></div>
</section>
<h2 class="services-title">OUR SERVICES</h2>
<div class="rule" style="left:576px;top:1497px"></div>

<div class="service-card" style="left:112px">
  <svg width="84" height="84" viewBox="0 0 84 84" fill="none" stroke="var(--ink)" stroke-width="2.5">
    <path d="M8 30 L42 6 L76 30"/><path d="M16 26 V80 M68 26 V80"/>
    <rect x="36" y="26" width="12" height="10"/>
    <path d="M4 52 H34 M4 80 H34 M50 52 H80 M50 80 H80"/>
    <path d="M4 52 V80 M34 52 V80 M50 52 V80 M80 52 V80 M4 52 L34 80 M34 52 L4 80 M50 52 L80 80 M80 52 L50 80"/>
  </svg>
  <div class="service-name">SCAFFOLDING</div>
  <p class="service-text">Sed ut perspiciatis unde omnis iste natus error sit voluptatem accusantium dolorem que laudantium, totam rem aperiam, eaq illo inventore explicabo.</p>
  <a class="btn-solid">READ MORE</a>
</div>

<div class="service-card" style="left:444px">
  <svg width="92" height="90" viewBox="0 0 92 90" fill="none" stroke="var(--ink)" stroke-width="2.5">
    <circle cx="46" cy="9" r="6"/><path d="M38 38 V20 H54 V38 M42 38 V48 M50 38 V48"/>
    <ellipse cx="46" cy="46" rx="20" ry="6"/>
    <path d="M4 46 L14 38 V42 H26 V50 H14 V54 Z M88 46 L78 38 V42 H66 V50 H78 V54 Z"/>
    <path d="M10 88 L30 68 M10 88 H20 M10 88 V78 M82 88 L62 68 M82 88 H72 M82 88 V78"/>
  </svg>
  <div class="service-name">PROJECT MANAGEMENT</div>
  <p class="service-text">Sed ut perspiciatis unde omnis iste natus error sit voluptatem accusantium dolorem que laudantium, totam rem aperiam, eaq illo inventore explicabo.</p>
  <a class="btn-solid">READ MORE</a>
</div>

<div class="service-card" style="left:776px">
  <svg width="76" height="82" viewBox="0 0 76 82" fill="none" stroke="var(--ink)" stroke-width="2.5">
    <rect x="4" y="4" width="68" height="74"/>
    <path d="M4 16 H24 M4 28 H24 M14 4 V28 M24 4 V28"/>
    <path d="M32 16 H64 M32 26 H64 M14 38 H64 M14 48 H64 M14 58 H64 M14 68 H64"/>
  </svg>
  <div class="service-name">SCREED &amp; INSULATION</div>
  <p class="service-text">Sed ut perspiciatis unde omnis iste natus error sit voluptatem accusantium dolorem que laudantium, totam rem aperiam, eaq illo inventore explicabo.</p>
  <a class="btn-solid">READ MORE</a>
</div>

<section class="contact"></section>
<h2 class="contact-title">CONTACT US</h2>

<div class="info-item" style="top:2141px">
  <svg width="32" height="42" viewBox="0 0 32 42" fill="none" stroke="#fff" stroke-width="1.6"><path d="M16 40 C6 26 2 20 2 14 A14 14 0 0 1 30 14 C30 20 26 26 16 40 Z"/><circle cx="16" cy="14" r="5"/></svg>
  <div class="info-label">ADDRESS</div>
  <div class="info-value">#215 Lorem Ipsum dummy text Lorem</div>
</div>
<div class="info-item" style="top:2243px">
  <svg width="38" height="40" viewBox="0 0 38 40" fill="none" stroke="#fff" stroke-width="1.6"><path d="M8 4 L14 12 L10 17 C13 24 17 28 23 31 L28 27 L35 33 L30 38 C16 36 4 24 2 10 Z"/><path d="M22 6 A12 12 0 0 1 33 17 M22 11 A7 7 0 0 1 28 17"/></svg>
  <div class="info-label">PHONE</div>
  <div class="info-value">000-47-5820</div>
</div>
<div class="info-item" style="top:2341px">
  <svg width="40" height="32" viewBox="0 0 40 32" fill="none" stroke="#fff" stroke-width="1.6"><rect x="1" y="3" width="38" height="26"/><path d="M1 3 L20 19 L39 3 M1 29 L15 15 M39 29 L25 15"/></svg>
  <div class="info-label">EMAIL</div>
  <div class="info-value">info@larvik-demo.at</div>
</div>

<div class="field" style="left:557px;top:2079px;width:230px">First Name</div>
<div class="field" style="left:841px;top:2079px;width:230px">Last Name</div>
<div class="field" style="left:557px;top:2155px;width:230px">Email</div>
<div class="field" style="left:841px;top:2155px;width:230px">Phone</div>
<div class="field" style="left:557px;top:2285px;width:512px">Message</div>
<a class="btn-submit">SUBMIT</a>
<span class="social" style="left:776px" role="img" aria-label="Social profile link 1"></span>
<span class="social" style="left:824px" role="img" aria-label="Social profile link 2"></span>
<span class="social" style="left:871px" role="img" aria-label="Social profile link 3"></span>

<footer class="site-footer">
  <p class="copyright">© Copyright 2021 Larvik.All Rights Reserved</p>
</footer>

</body>
</html>
```